Real estate broker business card

Want a modern celan but effective business card for my residential and commercial real estate business. I want the back of the card to advertise my services and to capture business. I have attached the back of my current business card fore ideas
Updates

Logos, photo and text updates added! Added Saturday, September 3, 2016

Project Deadline Extended Reason: LOGOS, PHOTOS AND TEST JUST UPLOADED! I'M READY TO PICK A DESIGN! THANK YOU! Added Saturday, September 3, 2016

Target Market(s)

home buyers and seller. commercial buyers and sellers

Industry/Entity Type

Real Estate

Contact Information for Business Card

must have my contact information and my photo

Requirements
Must have
• Carla Ventrino
• Owner & Qualifying Broker
• Ventrino Real Estate Services
• 505.718.2094
• carla@ventrinohomes.example
• www.ventrinohomes.example
Nice to have
• metallic
• Business capture text: " Don't buy or lease property without someone looking out for your best interests. I will represent you on your home or investment purchase for FREE!"
• "Home owners, call today to receive a FREE market analysis for your homes value!

```html
<!DOCTYPE html>
<html lang="en">
<head>
<meta charset="utf-8">
<title>Ventrino Real Estate Services – Business Card</title>
<link href="https://fonts.googleapis.com/css2?family=Cinzel:wght@600&family=Open+Sans:wght@400;600;700&display=swap" rel="stylesheet">
<style>
  :root {
    --page-bg: #e6e9f1;
    --card-black: #0a0a0a;
    --teal: #1f8f9b;
    --teal-light: #37a9b4;
    --text-grey: #a9abae;
    --photo-dark: #1a1411;
    --photo-mid: #5a4137;
    --photo-light: #c9b3a6;
    --photo-white: #e9e5e2;
  }
  * { box-sizing: border-box; margin: 0; padding: 0; }
  html, body {
    width: 1200px;
    height: 900px;
    overflow: hidden;
    background: var(--page-bg);
  }
  .canvas {
    width: 1200px;
    height: 900px;
    display: flex;
    flex-direction: column;
    align-items: center;
    justify-content: center;
    gap: 56px;
  }
  .card {
    position: relative;
    width: 630px;
    height: 360px;
    background: var(--card-black);
    overflow: hidden;
    box-shadow: 0 10px 28px rgba(40, 50, 80, 0.22);
  }

  /* Brand name (wordmark stand-in) */
  .brand {
    display: flex;
    align-items: center;
    gap: 12px;
  }
  .brand-dot {
    width: 34px;
    height: 34px;
    border-radius: 50%;
    background: var(--teal);
    flex: none;
  }
  .brand-name {
    font-family: "Open Sans", sans-serif;
    font-weight: 600;
    color: var(--teal);
    text-transform: uppercase;
    letter-spacing: 0.12em;
    line-height: 1.15;
  }

  /* Front */
  .card-front .brand {
    position: absolute;
    left: 30px;
    top: 28px;
  }
  .card-front .brand-name { font-size: 17px; }
  .contact {
    position: absolute;
    left: 40px;
    top: 104px;
    font-family: "Open Sans", sans-serif;
  }
  .contact-name {
    color: var(--teal-light);
    font-size: 16px;
    font-weight: 700;
  }
  .contact-title {
    color: var(--text-grey);
    font-size: 12.5px;
    margin-top: 2px;
  }
  .contact-list {
    list-style: none;
    margin-top: 14px;
  }
  .contact-list li {
    display: flex;
    align-items: center;
    gap: 9px;
    color: var(--text-grey);
    font-size: 13px;
    line-height: 1.7;
  }
  .contact-list svg {
    width: 11px;
    height: 11px;
    fill: var(--teal-light);
    flex: none;
  }
  .portrait {
    position: absolute;
    right: 0;
    bottom: 0;
    width: 330px;
    height: 250px;
    background:
      radial-gradient(ellipse 60% 70% at 58% 38%, var(--photo-light) 0%, var(--photo-mid) 35%, rgba(26,20,17,0) 72%),
      radial-gradient(ellipse 80% 45% at 55% 100%, var(--photo-white) 0%, rgba(233,229,226,0.6) 45%, rgba(233,229,226,0) 75%),
      linear-gradient(to left, var(--photo-dark), var(--card-black));
  }

  /* Back */
  .card-back {
    display: flex;
    align-items: center;
    justify-content: center;
  }
  .card-back .brand-name { font-size: 22px; }
</style>
</head>
<body>
  <main class="canvas">
    <section class="card card-front" aria-label="Business card front">
      <div class="brand">
        <span class="brand-dot"></span>
        <span class="brand-name">Ventrino Real Estate Services</span>
      </div>

      <div class="contact">
        <p class="contact-name">Carla Ventrino</p>
        <p class="contact-title">Owner &amp; Qualifying Broker</p>
        <ul class="contact-list">
          <li>
            <svg viewBox="0 0 12 12" aria-hidden="true"><path d="M2.4 0.8 4.2 0.5 5.2 3 4 4a7 7 0 0 0 4 4l1-1.2 2.5 1L11.2 9.6C10.8 11 9.6 11.6 8 11 4.7 9.8 2.2 7.3 1 4 0.5 2.4 1 1.2 2.4 0.8Z"/></svg>
            505.718.2094
          </li>
          <li>
            <svg viewBox="0 0 12 12" aria-hidden="true"><path d="M0.5 2h11v8h-11Z M1.5 3 6 6.6 10.5 3v-0.2h-9Z" fill-rule="evenodd"/></svg>
            carla@ventrinohomes.example
          </li>
          <li>
            <svg viewBox="0 0 12 12" aria-hidden="true"><path d="M6 0.5a5.5 5.5 0 1 0 0 11 5.5 5.5 0 0 0 0-11Zm0 1.5a4 4 0 1 1 0 8 4 4 0 0 1 0-8Z"/></svg>
            www.ventrinohomes.example
          </li>
        </ul>
      </div>

      <div class="portrait" role="img" aria-label="Portrait photo of the broker, smiling, in a white top against a black background"></div>
    </section>

    <section class="card card-back" aria-label="Business card back">
      <div class="brand">
        <span class="brand-dot"></span>
        <span class="brand-name">Ventrino Real Estate Services</span>
      </div>
    </section>
  </main>
</body>
</html>
```